Business card for wedding & event planning company

I'm looking for a well designed double sided business card to represent my wedding and event planning company.

It should include the fact we manage the following events:
Weddings, birthdays, conferences, product launches, fashion shows & conventions
in the following areas:
Wiltshire, Oxfordshire, Berkshire & London

My contact details to be included are:

Moira Stanwick
07514 283640
moira@bluefernevents.co.uk
www.bluefernevents.co.uk

My logo can be found at the following Filebarn location:
AI file: https://www.filebarn.example/s/k3mxpw8rt51bn7d/logo_sourcefile.ai
PNG file:
https://www.filebarn.example/s/h6qvlz2ncy90tue/logo_image.png

Target Market(s)

women aged 30-55

Industry/Entity Type

Wedding

Contact Information for Business Card

in the following areas:

Moira Stanwick
Event Planner
07514 283640

Font styles to use
Serif
Sans Serif
Script

Requirements
Must have
• Purple and white colour scheme
Should not have
• Black background
• Please don't submit any of the see-through business card designs.

```html
<!DOCTYPE html>
<html lang="en">
<head>
<meta charset="utf-8">
<title>Blue Fern Events – Business Card</title>
<link rel="stylesheet" href="https://fonts.googleapis.com/css2?family=Open+Sans:wght@400;600&display=swap">
<style>
  :root {
    --backdrop: #2a2521;
    --card: #3b2050;
    --card-light: #4a2a63;
    --card-dark: #2f1942;
    --card-edge: #553070;
    --purple-accent: #d49cf0;
    --silver: #e6dcec;
    --white: #ffffff;
    --rule: #6e4a88;
  }
  * { margin: 0; padding: 0; box-sizing: border-box; }
  html, body {
    width: 1200px; height: 844px; overflow: hidden;
    background: var(--backdrop);
    font-family: "Open Sans", Arial, sans-serif;
  }
  .canvas { position: relative; width: 1200px; height: 844px; }
  .card {
    position: absolute; top: 262px;
    width: 520px; height: 320px;
    background: linear-gradient(160deg, var(--card-light) 0%, var(--card) 60%, var(--card-dark) 100%);
    border: 1px solid var(--card-edge);
  }
  .card--contact { left: 60px; }
  .card--services { left: 620px; }

  /* brand lockup */
  .brand { position: absolute; display: flex; align-items: center; gap: 12px; }
  .brand__mark {
    width: 44px; height: 44px; border-radius: 50%;
    border: 2px solid currentColor; flex: none;
  }
  .brand__name { font-size: 22px; font-weight: 400; letter-spacing: 0.5px; white-space: nowrap; }

  /* contact side */
  .card--contact .brand { left: 28px; top: 196px; color: var(--purple-accent); }
  .card--contact .divider {
    position: absolute; left: 270px; top: 60px; width: 1px; height: 220px;
    background: var(--rule);
  }
  .contact { position: absolute; left: 292px; top: 82px; }
  .contact__name { color: var(--purple-accent); font-size: 19px; font-weight: 400; margin-bottom: 28px; }
  .contact__list { list-style: none; font-size: 13.5px; color: var(--white); line-height: 1.55; }
  .contact__label { color: var(--purple-accent); margin-right: 4px; }

  /* services side */
  .card--services .brand { left: 40px; top: 118px; color: var(--silver); }
  .card--services .brand__name { font-size: 26px; }
  .card--services .rule {
    position: absolute; left: 40px; top: 196px; width: 250px; height: 1px;
    background: var(--rule);
  }
  .services {
    position: absolute; right: 34px; top: 34px; list-style: none;
    color: var(--white); font-size: 12.5px; line-height: 1.5;
  }
  .areas {
    position: absolute; left: 40px; top: 214px;
    color: var(--white); font-size: 13px; letter-spacing: 0.3px;
  }
</style>
</head>
<body>
<main class="canvas">
  <section class="card card--contact" aria-label="Contact side">
    <div class="brand">
      <span class="brand__mark"></span>
      <span class="brand__name">Blue Fern Events</span>
    </div>
    <div class="divider"></div>
    <div class="contact">
      <h1 class="contact__name">Moira Stanwick</h1>
      <ul class="contact__list">
        <li><span class="contact__label">T:</span>07514 283640</li>
        <li><span class="contact__label">E:</span>moira@bluefernevents.co.uk</li>
        <li><span class="contact__label">W:</span>www.bluefernevents.co.uk</li>
      </ul>
    </div>
  </section>

  <section class="card card--services" aria-label="Services side">
    <ul class="services">
      <li>.Weddings</li>
      <li>.Birthdays</li>
      <li>.Conferences</li>
      <li>.Product Launches</li>
      <li>.Fashion Shows</li>
      <li>.Conventions</li>
    </ul>
    <div class="brand">
      <span class="brand__mark"></span>
      <span class="brand__name">Blue Fern Events</span>
    </div>
    <div class="rule"></div>
    <p class="areas">Wiltshire &nbsp;-&nbsp; Oxfordshire &nbsp;-&nbsp; Berkshire &nbsp;-&nbsp; London</p>
  </section>
</main>
</body>
</html>
```